Visitenkarten-Design für virtuelle Jobmesse & Jobbörse für Soldaten
Zielgruppe
Die KVL GmbH ist ein Unternehmen das zwei Hauptprodukte betreibt! Zum einen Jobbörse für Soldaten unter www.laufbahnwechsel-beispiel.de und zum anderen eine virtuelle Jobmesse für Soldaten unter www.merivon-beispiel.de , die wir zweimal im Jahr veranstalten.
Aufgabenstellung
Wir haben ja die beiden Produkte Laufbahnwechsel.de und die Merivon, für die bereits jeweils ein separtes Logo besteht! Diese finden Sie im Anhang! Beide werden doch jedoch von einem Unternehmen, der KVL GmbH betrieben! Aktuell nutzen wir eine Visitenkarte mit dem Logo von KVL und eine mit dem Logo der MERIVON. Gerade im Hinblick darauf, dass wir zukünftig auch weiter Plattformen in unser Portfolio aufnehmen, möchte ich hier unsere V-Karten flexibler gestalten!
Ziel soll es also sein, eine Visitenkarte zu gestalten, auf dem klar wird, dass der Mitarbeiter von der KVL GmbH kommt, die KVL GmbH aber unterschiedliche Produkte betreibt.
Im Anhang finden Sie:
1. Das Logo von KVL
2. Das Logo von Merivon
3. Die aktuelle V-Karte von KVL
4. Die aktuelle V-Karte von MERIVON
Vielleicht ein kleiner Anreiz: Aktuell nutzen wir auch zwei getrennte Geschäftspapiere. Das von www.laufbahnwechsel-beispiel.de lade ich einmal hoch! Der Designer, der auch die Visitenkarte erstellt, erhällt im Anschluss den 1:1 Auftrag in Höhe von 200 Euro für die Erstellung des Geschäftspapiers! Wenn Sie jetzt schon einen Vorschlag für das Geschäftspapier einreichen, erhöht das natürlich Ihre Chancen, wobei ich verspreche, dass wir im Falle eine Annahme das 1:1 im Anschluß dennoch starten werden!

```html
<!DOCTYPE html>
<html lang="de">
<head>
<meta charset="utf-8">
<title>KVL GmbH – Geschäftsausstattung</title>
<link href="https://fonts.googleapis.com/css2?family=Arimo:wght@400;700&display=swap" rel="stylesheet">
<style>
  :root{
    --bg:#f7ebdb;
    --blue:#234e8c;
    --green:#3a5a2a;
    --grey:#8a8a8a;
    --text:#3a3a3a;
    --dark:#2a2a2a;
    --flap:#646464;
    --paper:#ffffff;
  }
  *{box-sizing:border-box;margin:0;padding:0}
  html,body{width:1200px;height:1000px;overflow:hidden;background:var(--bg);font-family:"Arimo",Arial,sans-serif;color:var(--text)}
  .canvas{position:relative;width:1200px;height:1000px}
  .sheet{position:absolute;background:var(--paper);box-shadow:4px 5px 7px rgba(0,0,0,.35);overflow:hidden}
  .abs{position:absolute}

  .rule{position:absolute;left:0;right:0;height:4px;border-top:1.5px solid var(--blue);border-bottom:1.5px solid var(--grey)}

  .brand{position:absolute;text-align:center;background:var(--paper);padding:2px 3px}
  .brand-name{display:block;color:var(--blue);font-weight:700;line-height:1;white-space:nowrap}
  .company{display:block;color:var(--text);font-weight:700;line-height:1;white-space:nowrap}
  .product{display:flex;align-items:center;justify-content:center;gap:3px;color:var(--green);font-weight:700;line-height:1}
  .product .dot{border-radius:50%;background:var(--green);display:inline-block}
  .product-url{display:block;color:var(--green);font-weight:700;line-height:1;white-space:nowrap}
  .product-note{display:block;color:var(--text);font-weight:700;line-height:1;white-space:nowrap}

  .band{position:absolute;left:0;right:0;bottom:0;color:#fff;font-weight:700;
    background:linear-gradient(110deg,var(--green) 0 44%,#fff 44% 45%,#6a6a6a 45% 47%,#fff 47% 48%,#6a6a6a 48% 50%,#fff 50% 51%,#6a6a6a 51% 53%,#fff 53% 54%,var(--blue) 54%)}
  .band span{position:absolute;top:50%;transform:translateY(-50%);white-space:nowrap}

  .small{font-size:5px;line-height:1.6}
  .blue{color:var(--blue)}
  .nowrap{white-space:nowrap}
</style>
</head>
<body>
<div class="canvas">

  <!-- Briefbogen -->
  <section class="sheet letterhead" style="left:76px;top:63px;width:420px;height:594px">
    <div class="rule" style="top:32px"></div>
    <div class="brand" style="left:324px;top:20px;width:78px">
      <span class="brand-name" style="font-size:8px">Laufbahnwechsel</span>
      <span class="company" style="font-size:8px;margin-top:10px">KVL GmbH</span>
      <span class="product" style="font-size:7px;margin-top:14px"><i class="dot" style="width:4px;height:4px"></i>MERIVON</span>
      <span class="product-url" style="font-size:6.5px;margin-top:6px">Merivon.de</span>
      <span class="product-note" style="font-size:4.5px;margin-top:4px">ist eine Marke der KVL GmbH</span>
    </div>
    <div class="abs window" style="left:38px;top:79px;width:174px;height:84px">
      <svg width="174" height="84" viewBox="0 0 174 84" aria-hidden="true">
        <g fill="none" stroke="#999" stroke-width=".8">
          <path d="M1 14 V8 Q1 1 8 1 H14"/><path d="M160 1 H166 Q173 1 173 8 V14"/>
          <path d="M1 70 V76 Q1 83 8 83 H14"/><path d="M160 83 H166 Q173 83 173 76 V70"/>
        </g>
      </svg>
      <p class="abs nowrap" style="left:23px;top:5px;font-size:5px"><b>KVL GMBH</b> • Lindenweg 7 • 86999 Musterfeld</p>
    </div>
    <address class="abs small nowrap" style="right:24px;top:122px;text-align:right;font-style:normal">
      <b>KVL GMBH</b><br>Lindenweg 7<br>86999 Musterfeld<br>
      <span style="display:block;margin-top:3px"><span class="blue">Telef.:</span> 08431 - 555 20 17</span>
      <span style="display:block;margin-top:2px"><span class="blue">Mobil.:</span> 0170 - 555 31 642</span>
      <span style="display:block;margin-top:2px"><span class="blue">E.:</span> weber@merivon-beispiel.de</span>
      <span style="display:block;margin-top:2px"><span class="blue">E.:</span> weber@laufbahnwechsel-beispiel.de</span>
    </address>
    <div class="abs" style="left:0;right:0;top:550px;border-top:1px solid #ccc"></div>
    <p class="abs" style="left:0;right:0;top:555px;text-align:center;font-size:5px;color:#888;line-height:2">
      Bank: Sparkasse Beispielstadt • IBAN: DE 00 1234 5678 9012 3456 78 • BIC-Swift: BSPLDE00XXX<br>
      Amtsgericht Musterstadt • Handelsregister: HRB 01234 • USt.-ID-Nr.: DE000123456
    </p>
    <div class="band" style="height:17px;font-size:9.5px">
      <span style="left:62px">www.merivon-beispiel.de</span>
      <span style="left:240px">www.laufbahnwechsel-beispiel.de</span>
    </div>
  </section>

  <!-- Umschlag Rückseite grau -->
  <section class="abs envelope-grey" style="left:68px;top:684px;width:440px;height:282px">
    <div class="sheet" style="left:0;top:62px;width:440px;height:220px"></div>
    <svg class="abs" style="left:0;top:0" width="440" height="126" viewBox="0 0 440 126" aria-hidden="true">
      <path d="M26 0 H412 Q418 0 420 6 L440 62 L422 118 Q420 124 412 124 H28 Q22 124 20 118 L0 62 L18 6 Q20 0 26 0 Z" fill="var(--flap)"/>
      <line x1="0" y1="62" x2="440" y2="62" stroke="#555" stroke-width=".8"/>
    </svg>
  </section>

  <!-- Visitenkarte Vorderseite -->
  <section class="sheet card-front" style="left:543px;top:55px;width:292px;height:189px">
    <h1 class="abs blue nowrap" style="left:27px;top:15px;font-size:16px;font-weight:400;line-height:1">Jonas Weber</h1>
    <p class="abs nowrap" style="left:27px;top:31px;font-size:8.5px;letter-spacing:.4px;line-height:1">Geschäftsführer</p>
    <div class="rule" style="top:42px"></div>
    <div class="brand" style="left:188px;top:36px;width:96px">
      <span class="brand-name" style="font-size:10px">Laufbahnwechsel</span>
      <span class="company" style="font-size:11px;margin-top:21px">KVL GmbH</span>
      <span class="product" style="font-size:9px;margin-top:20px"><i class="dot" style="width:6px;height:6px"></i>MERIVON</span>
      <span class="product-url" style="font-size:9.5px;margin-top:16px">Merivon.de</span>
      <span class="product-note" style="font-size:6px;margin-top:6px">ist eine Marke der KVL GmbH</span>
    </div>
    <address class="abs nowrap" style="left:26px;top:56px;font-size:9.5px;line-height:1.25;font-style:normal">
      <b>KVL GMBH</b><br>Lindenweg 7<br>86999 Musterfeld
    </address>
    <div class="abs nowrap" style="left:17px;top:98px;width:168px;font-size:9px;line-height:15px">
      <p><span class="blue" style="display:inline-block;width:53px">Telefon.:</span>08431 - 555 20 17</p>
      <p><span class="blue" style="display:inline-block;width:53px">Mobil.:</span>0170 - 555 31 642</p>
      <p style="font-size:8px"><span class="blue">E.:</span> weber@laufbahnwechsel-beispiel.de</p>
      <p style="font-size:8px"><span class="blue">E.:</span> weber@merivon-beispiel.de</p>
    </div>
    <div class="band" style="height:17px;font-size:9px">
      <span style="left:17px">www.merivon-beispiel.de</span>
      <span style="left:163px;font-size:7px">www.laufbahnwechsel-beispiel.de</span>
    </div>
  </section>

  <!-- Visitenkarte Rückseite -->
  <section class="sheet card-back" style="left:862px;top:55px;width:291px;height:189px;background:var(--dark)">
    <div class="rule" style="top:70px;border-bottom-color:#999"></div>
    <p class="abs nowrap" style="left:75px;width:141px;top:60px;padding:5px 0;text-align:center;background:var(--dark);color:#d0d0d0;font-size:15px;font-weight:700">Laufbahnwechsel</p>
    <p class="product abs" style="left:0;right:0;top:128px;font-size:14px"><i class="dot" style="width:8px;height:8px"></i>MERIVON</p>
  </section>

  <!-- Kurzmitteilung -->
  <section class="sheet compliment" style="left:652px;top:273px;width:440px;height:223px">
    <div class="rule" style="top:32px"></div>
    <div class="brand" style="left:30px;top:27px;width:66px">
      <span class="brand-name" style="font-size:6.5px">Laufbahnwechsel</span>
      <span class="company" style="font-size:7px;margin-top:11px">KVL GmbH</span>
      <span class="product" style="font-size:6px;margin-top:12px"><i class="dot" style="width:4px;height:4px"></i>MERIVON</span>
      <span class="product-url" style="font-size:5.5px;margin-top:9px">Merivon.de</span>
      <span class="product-note" style="font-size:4px;margin-top:3px">ist eine Marke der KVL GmbH</span>
    </div>
    <p class="abs nowrap" style="left:96px;top:39px;font-size:6.5px"><b>KVL GMBH</b> Lindenweg 7 • 86999 Musterfeld</p>
    <div class="band" style="height:17px;font-size:9.5px">
      <span style="left:66px">www.merivon-beispiel.de</span>
      <span style="left:255px">www.laufbahnwechsel-beispiel.de</span>
    </div>
  </section>

  <!-- Umschlag Vorderseite -->
  <section class="sheet envelope-front" style="left:652px;top:509px;width:440px;height:224px">
    <div class="rule" style="top:137px"></div>
    <div class="brand" style="left:277px;top:132px;width:68px">
      <span class="brand-name" style="font-size:6.5px">Laufbahnwechsel</span>
      <span class="company" style="font-size:7px;margin-top:10px">KVL GmbH</span>
      <span class="product" style="font-size:6px;margin-top:12px"><i class="dot" style="width:4px;height:4px"></i>MERIVON</span>
      <span class="product-url" style="font-size:5.5px;margin-top:8px">Merivon.de</span>
      <span class="product-note" style="font-size:4px;margin-top:3px">ist eine Marke der KVL GmbH</span>
    </div>
    <address class="abs nowrap" style="right:30px;top:183px;text-align:right;font-size:6.5px;line-height:1.4;font-style:normal">
      <b>KVL GMBH</b><br>Lindenweg 7<br>86999 Musterfeld
    </address>
  </section>

  <!-- Umschlag Rückseite -->
  <section class="sheet envelope-back" style="left:652px;top:746px;width:440px;height:220px">
    <svg class="abs" style="left:0;top:0" width="440" height="70" viewBox="0 0 440 70" aria-hidden="true">
      <path d="M2 0 L28 58 Q32 63 40 63 H400 Q408 63 411 58 L438 0" fill="none" stroke="#999" stroke-width=".8"/>
    </svg>
    <div class="rule" style="top:31px;left:12px;right:12px"></div>
    <p class="brand" style="left:188px;width:64px;top:28px;padding:0"><span class="brand-name" style="font-size:6.5px">Laufbahnwechsel</span></p>
  </section>

</div>
</body>
</html>
```